New Business Card Design Project

We require a business card design for Vexalund, a newly established Indian company.
Our focus is on the development, manufacturing, and export of a diverse array of pharmaceutical products on a global scale. The card should convey a professional appearance, as our primary markets are in Africa, China, and Southeast Asian nations.
We envision a two-sided business card, with the reverse side dedicated to a logo set against a solid color or an elegantly designed pattern. The corners should be rounded. We would appreciate seeing both horizontal and vertical design options. We trust the designer to utilize their expertise in creating this design.

The content for the business card is included in the attached Word file.

Target Market(s)

Our primary markets are in Africa, China, and Southeast Asian, Latin America, Maldives, Sri Lanka

Industry/Entity Type

Pharmaceutical Manufacturing and Export

Contact Information for Business Card

Colors

Designer to choose colors to be used in the design.

Requirements
Must have
• The reverse side of the business card features solely the logo along with the tagline, "Care for Every Day."
Should not have
• The logo should not exceed two instances, encompassing both the front and back sides of the card.

```html
<!DOCTYPE html>
<html lang="en">
<head>
<meta charset="utf-8">
<title>Vexalund Business Card</title>
<link rel="stylesheet" href="https://fonts.googleapis.com/css2?family=Open+Sans:wght@400;600;700&display=swap">
<style>
  :root {
    --stage: #222222;
    --paper: #ffffff;
    --coral: #ee5f4b;
    --blue: #2ea7e0;
    --ink: #1c1c1c;
  }
  * { box-sizing: border-box; margin: 0; padding: 0; }
  html, body { width: 1200px; height: 711px; overflow: hidden; }
  body {
    background: var(--stage);
    font-family: "Open Sans", Arial, sans-serif;
    position: relative;
  }
  .card {
    position: absolute;
    background: var(--paper);
    border: 3px solid var(--coral);
  }
  .card-back {
    left: 70px; top: 205px;
    width: 540px; height: 310px;
    border-radius: 120px 0 120px 0;
  }
  .card-front {
    left: 740px; top: 90px;
    width: 320px; height: 530px;
    border-radius: 0 120px 0 120px;
  }
  .brand {
    display: flex; align-items: center; gap: 10px;
    color: var(--blue); font-weight: 700;
  }
  .brand-dot { border-radius: 50%; background: var(--coral); }
  .card-back .brand {
    position: absolute; left: 95px; top: 105px; font-size: 62px; letter-spacing: -1px;
  }
  .card-back .brand-dot { width: 22px; height: 22px; }
  .tagline {
    position: absolute; right: 95px; top: 196px;
    font-size: 15px; color: var(--ink);
  }
  .card-front .brand {
    position: absolute; left: 0; right: 0; top: 70px; justify-content: center;
    font-size: 36px;
  }
  .card-front .brand-dot { width: 14px; height: 14px; }
  .person { position: absolute; left: 40px; top: 300px; }
  .person-name { font-size: 26px; color: var(--blue); font-weight: 400; white-space: nowrap; }
  .person-name strong { font-weight: 700; }
  .person-role { font-size: 14px; font-weight: 600; color: var(--ink); margin-top: 2px; }
  .address { position: absolute; left: 40px; top: 372px; font-size: 12.5px; line-height: 1.5; color: var(--ink); }
  .contacts { position: absolute; left: 40px; top: 420px; list-style: none; font-size: 12.5px; color: var(--ink); }
  .contacts li { display: flex; align-items: center; gap: 8px; line-height: 1.7; }
  .contacts svg { width: 13px; height: 13px; flex: none; }
</style>
</head>
<body>
  <section class="card card-back" aria-label="Card reverse">
    <div class="brand"><span class="brand-dot"></span>Vexalund</div>
    <p class="tagline">Care for Every Day.</p>
  </section>

  <section class="card card-front" aria-label="Card front">
    <div class="brand"><span class="brand-dot"></span>Vexalund</div>
    <div class="person">
      <p class="person-name"><strong>Arjun</strong> K. Malhotra</p>
      <p class="person-role">CEO</p>
    </div>
    <p class="address">12, Sagar Nagar,<br>Nashik, 422005, India</p>
    <ul class="contacts">
      <li>
        <svg viewBox="0 0 14 14"><rect x="3" y="1" width="8" height="12" rx="1.5" fill="none" stroke="var(--coral)" stroke-width="1.6"/></svg>
        +919 555018274
      </li>
      <li>
        <svg viewBox="0 0 14 14"><circle cx="7" cy="7" r="6" fill="var(--blue)"/><path d="M1 7h12M7 1c-3 3-3 9 0 12M7 1c3 3 3 9 0 12" fill="none" stroke="#fff" stroke-width="0.9"/></svg>
        www.vexalund.com
      </li>
      <li>
        <svg viewBox="0 0 14 14"><rect x="1" y="3" width="12" height="9" fill="var(--coral)"/><path d="M1 3l6 5 6-5" fill="none" stroke="#fff" stroke-width="1.1"/></svg>
        amalhotra@vexalund.com
      </li>
    </ul>
  </section>
</body>
</html>
```